Oil Field Service company needs professional business cards

Looking to clean up our current company business cards and look a little more professional. Brenwick Casing Services is a US based company that services the oil field. We deal with engineers, managers and oil rigs....................................................................................................................................................................................................................................................................................................................................................................................................

Target Market(s)

Oil and Gas professionals

Industry/Entity Type

Oil And Gas

Contact Information for Business Card

See attached photo as example

Font styles to use
Sans Serif

Colors
ec1f27

Requirements
Must have
• Company Logo, Name, Title, Cell, Office, Fax, Email.
• See attached photo
Nice to have
• External CRT, Internal CRT, Casing Crews, Torque Turn, Laydown Machine
Should not have
• Do not introduce any new pictures and keep it professional looking

```html
<!DOCTYPE html>
<html lang="en">
<head>
<meta charset="UTF-8">
<title>Brenwick Casing Services – Business Cards</title>
<link href="https://fonts.googleapis.com/css2?family=Open+Sans:wght@400;600;700&display=swap" rel="stylesheet">
<style>
  :root {
    --page-bg: #ecebe8;
    --slate: #465563;
    --brand-red: #ec1f27;
    --white: #ffffff;
    --text-dark: #3d4a57;
  }
  * { box-sizing: border-box; margin: 0; padding: 0; }
  html, body { width: 1200px; height: 900px; overflow: hidden; }
  body {
    background: var(--page-bg);
    font-family: "Open Sans", Arial, sans-serif;
    display: flex;
    align-items: center;
    justify-content: center;
    gap: 60px;
  }
  .card {
    width: 520px;
    height: 297px;
    position: relative;
    overflow: hidden;
    box-shadow: 0 6px 18px rgba(0,0,0,0.18);
  }

  /* Shared wordmark */
  .wordmark {
    font-weight: 700;
    text-align: center;
    line-height: 1.1;
  }
  .wordmark-main { font-size: 40px; letter-spacing: 1px; display: block; }
  .wordmark-sub { font-size: 14px; letter-spacing: 6px; display: block; text-transform: uppercase; margin-top: 4px; }

  /* Back card */
  .card-back {
    background: var(--slate);
    color: var(--white);
    display: flex;
    flex-direction: column;
    align-items: center;
    justify-content: center;
    gap: 34px;
  }
  .card-back .wordmark { color: var(--white); }
  .service-list {
    list-style: none;
    display: flex;
    flex-wrap: wrap;
    justify-content: center;
    max-width: 420px;
    column-gap: 22px;
    row-gap: 8px;
    font-size: 14px;
  }
  .service-list li::before {
    content: "";
    display: inline-block;
    width: 6px; height: 6px;
    border-radius: 50%;
    background: var(--white);
    margin-right: 10px;
    vertical-align: middle;
  }

  /* Front card */
  .card-front { background: var(--white); }
  .front-header {
    position: absolute;
    left: 0; right: 0; top: 0;
    height: 132px;
    display: flex;
    align-items: center;
    justify-content: center;
    padding-left: 110px;
  }
  .card-front .wordmark { color: var(--text-dark); }
  .front-band {
    position: absolute;
    left: 0; right: 0; top: 132px;
    height: 110px;
    background: var(--brand-red);
    color: var(--white);
  }
  .phone-list {
    position: absolute;
    right: 22px; top: 10px;
    list-style: none;
    font-size: 12px;
    line-height: 1.5;
  }
  .phone-list li { display: flex; align-items: center; justify-content: flex-end; gap: 6px; }
  .phone-list svg { width: 10px; height: 10px; fill: var(--white); flex: none; }
  .contact-person {
    position: absolute;
    left: 36px; bottom: 12px;
  }
  .person-name { font-size: 21px; font-weight: 700; line-height: 1.2; }
  .person-title { font-size: 14px; padding-left: 14px; }
  .person-location { font-size: 15px; padding-left: 24px; margin-top: 4px; }
  .front-footer {
    position: absolute;
    left: 0; right: 0; bottom: 0;
    height: 55px;
    background: var(--slate);
    color: var(--white);
    display: flex;
    align-items: center;
    justify-content: flex-end;
    padding-right: 60px;
    font-size: 14px;
  }
</style>
</head>
<body>

  <section class="card card-back" aria-label="Business card back">
    <div class="wordmark">
      <span class="wordmark-main">BRENWICK</span>
      <span class="wordmark-sub">Casing Services</span>
    </div>
    <ul class="service-list">
      <li>External CRT</li>
      <li>Internal CRT</li>
      <li>Casing Crews</li>
      <li>Torque Turn</li>
      <li>Laydown Machine</li>
    </ul>
  </section>

  <section class="card card-front" aria-label="Business card front">
    <header class="front-header">
      <div class="wordmark">
        <span class="wordmark-main">BRENWICK</span>
        <span class="wordmark-sub">Casing Services</span>
      </div>
    </header>

    <div class="front-band">
      <ul class="phone-list">
        <li>(555) 410-2200
          <svg viewBox="0 0 10 10" aria-label="Office"><path d="M1 3c0-1 1-2 4-2s4 1 4 2v1H7V3H3v1H1zM2 5h6l1 4H1z"/></svg>
        </li>
        <li>(555) 410-2231
          <svg viewBox="0 0 10 10" aria-label="Fax"><path d="M3 1h4v3H3zM1 4h8v5H1zM3 6h4v1H3z"/></svg>
        </li>
        <li>(555) 482-9017
          <svg viewBox="0 0 10 10" aria-label="Cell"><path d="M3 0h4a1 1 0 0 1 1 1v8a1 1 0 0 1-1 1H3a1 1 0 0 1-1-1V1a1 1 0 0 1 1-1zM3 1.5v6h4v-6z"/></svg>
        </li>
      </ul>
      <div class="contact-person">
        <p class="person-name">Carson Whitfield</p>
        <p class="person-title">Area Manager</p>
        <p class="person-location">Ridgeview, OK 74012</p>
      </div>
    </div>

    <footer class="front-footer">
      <p>E: cwhitfield@brenwickcasing.com</p>
    </footer>
  </section>

</body>
</html>
```